Step and Repeat Backdrop for wedding reception photo booth

Would like to have a Step and Repeat Backdrop (8 foot high by 10 foot wide) that incorporates the wedding logo (attached) and the names Helen and Gavin. Background should be white, and wedding colors are burgundy and gold. Show me creativity :-) I have included some random samples.

```html
<!DOCTYPE html>
<html lang="en">
<head>
<meta charset="utf-8">
<title>Helen &amp; Gavin — Step and Repeat Backdrop</title>
<link rel="stylesheet" href="https://fonts.googleapis.com/css2?family=Cinzel:wght@600&family=Great+Vibes&display=swap">
<style>
  :root {
    --canvas: #ffffff;
    --burgundy: #821424;
    --gold: #c9a25a;
    --grid-line: #ebd3d8;
    --row-h: 149.33px;
  }
  * { margin: 0; padding: 0; box-sizing: border-box; }
  html, body {
    width: 1200px; height: 1200px; overflow: hidden;
    background: var(--canvas);
  }
  .backdrop {
    position: absolute;
    left: 40px; top: 152px;
    width: 1120px; height: 896px;
    border: 1.5px solid var(--burgundy);
    background: var(--canvas);
    overflow: hidden;
  }
  .grid-lines { position: absolute; inset: 0; width: 100%; height: 100%; }
  .grid-lines line { stroke: var(--grid-line); stroke-width: 1.2; }
  .monogram {
    position: absolute;
    transform: translate(-50%, -50%);
    font-family: "Cinzel", serif;
    font-weight: 600;
    font-size: 50px;
    letter-spacing: -2px;
    color: var(--gold);
    white-space: nowrap;
    line-height: 1;
  }
  .name-banner {
    position: absolute;
    left: 317px; top: 149.33px;
    width: 485px; height: 149.33px;
    background: var(--burgundy);
    display: flex; align-items: center; justify-content: center;
  }
  .couple-names {
    font-family: "Great Vibes", cursive;
    font-size: 74px;
    color: var(--gold);
    font-weight: 400;
    white-space: nowrap;
  }
</style>
</head>
<body>
  <section class="backdrop" aria-label="Step and repeat backdrop">
    <svg class="grid-lines" viewBox="0 0 1120 896" preserveAspectRatio="none" aria-hidden="true">
      <!-- horizontal row dividers -->
      <line x1="0" y1="149.33" x2="1120" y2="149.33"/>
      <line x1="0" y1="298.67" x2="1120" y2="298.67"/>
      <line x1="0" y1="448" x2="1120" y2="448"/>
      <line x1="0" y1="597.33" x2="1120" y2="597.33"/>
      <line x1="0" y1="746.67" x2="1120" y2="746.67"/>
      <!-- rows 1, 3, 5 -->
      <line x1="187" y1="0" x2="187" y2="149.33"/>
      <line x1="560" y1="0" x2="560" y2="149.33"/>
      <line x1="933" y1="0" x2="933" y2="149.33"/>
      <line x1="187" y1="298.67" x2="187" y2="448"/>
      <line x1="560" y1="298.67" x2="560" y2="448"/>
      <line x1="933" y1="298.67" x2="933" y2="448"/>
      <line x1="187" y1="597.33" x2="187" y2="746.67"/>
      <line x1="560" y1="597.33" x2="560" y2="746.67"/>
      <line x1="933" y1="597.33" x2="933" y2="746.67"/>
      <!-- rows 4, 6 -->
      <line x1="373" y1="448" x2="373" y2="597.33"/>
      <line x1="747" y1="448" x2="747" y2="597.33"/>
      <line x1="373" y1="746.67" x2="373" y2="896"/>
      <line x1="747" y1="746.67" x2="747" y2="896"/>
    </svg>

    <div class="name-banner">
      <h1 class="couple-names">Helen &amp; Gavin</h1>
    </div>

    <span class="monogram" style="left:373px; top:74.7px">H&amp;G</span>
    <span class="monogram" style="left:747px; top:74.7px">H&amp;G</span>

    <span class="monogram" style="left:187px; top:224px">H&amp;G</span>
    <span class="monogram" style="left:933px; top:224px">H&amp;G</span>

    <span class="monogram" style="left:373px; top:373.3px">H&amp;G</span>
    <span class="monogram" style="left:747px; top:373.3px">H&amp;G</span>

    <span class="monogram" style="left:187px; top:522.7px">H&amp;G</span>
    <span class="monogram" style="left:560px; top:522.7px">H&amp;G</span>
    <span class="monogram" style="left:933px; top:522.7px">H&amp;G</span>

    <span class="monogram" style="left:373px; top:672px">H&amp;G</span>
    <span class="monogram" style="left:747px; top:672px">H&amp;G</span>

    <span class="monogram" style="left:187px; top:821.3px">H&amp;G</span>
    <span class="monogram" style="left:560px; top:821.3px">H&amp;G</span>
    <span class="monogram" style="left:933px; top:821.3px">H&amp;G</span>
  </section>
</body>
</html>
```